Business Card Design & Gift cards, Gift Cert, Donation Card

Retail Gift Store-in addition to Business Cards we'd like sequenced 2 sided Gift cards, Gift Certificate Cards, and Donation Cards.please see examples and email for clarificationlogos attached with examples-
Gift Card, Gift Certificate and Donation Card will all be same style just differant upper right title, with back side info as example.
business card, as example is single sided.
looking for additional ideas for layout

Industry/Entity Type

Business

Contact Information for Business Card

211 Newman St.East Tawas, MI 48730989.362.8730Office@BrewKrew.com

Requirements
Must have
• Blue as per example
• Logos provided
• like gradiant background

```html
<!DOCTYPE html>
<html lang="en">
<head>
<meta charset="utf-8">
<title>Tillow Marsh – Business Card &amp; Gift Card</title>
<link rel="stylesheet" href="https://fonts.googleapis.com/css2?family=Comic+Neue:wght@400;700&display=swap">
<style>
  :root {
    --backdrop: #5a5a5a;
    --card: #ffffff;
    --ink: #111111;
    --ink-soft: #555555;
    --rule: #6e6e6e;
    --brand-blue: #1a2fc4;
    --sun-yellow: #f4d21c;
  }
  html, body {
    margin: 0;
    width: 1105px;
    height: 1200px;
    overflow: hidden;
    background: var(--backdrop);
    font-family: "Comic Neue", "Comic Sans MS", cursive;
  }
  .card {
    position: absolute;
    left: 196px;
    width: 720px;
    height: 412px;
    background: var(--card);
    border-radius: 25px;
  }
  .card--business { top: 146px; }
  .card--gift { top: 602px; }

  .brand-name {
    position: absolute;
    right: 38px;
    top: 42px;
    margin: 0;
    font-size: 56px;
    font-weight: 400;
    letter-spacing: 1px;
    color: var(--ink);
    line-height: 1;
  }
  .divider {
    position: absolute;
    left: 38px;
    right: 38px;
    top: 257px;
    border-top: 2px solid var(--rule);
  }
  .contact, .offerings {
    position: absolute;
    top: 270px;
    margin: 0;
    padding: 0;
    list-style: none;
    font-size: 22px;
    line-height: 26.5px;
    color: var(--ink-soft);
  }
  .contact { left: 38px; }
  .offerings { right: 38px; text-align: right; }
  .contact li { display: flex; align-items: center; }
  .contact svg { width: 18px; height: 18px; margin-right: 10px; fill: var(--ink); }

  .card-number {
    position: absolute;
    right: 38px;
    top: 33px;
    font-size: 18px;
    color: var(--ink);
  }
  .field {
    position: absolute;
    display: flex;
    align-items: flex-end;
    color: var(--ink);
  }
  .field__label { white-space: nowrap; padding-right: 10px; }
  .field__line { flex: 1; border-bottom: 1.5px solid var(--rule); margin-bottom: 6px; }
  .field--large { left: 58px; right: 62px; font-size: 27px; }
  .field--small { left: 55px; width: 476px; font-size: 21px; }
  .field--to { top: 78px; }
  .field--from { top: 136px; }
  .field--issued { top: 222px; }
  .field--expires { top: 270px; }
  .field--employee { top: 318px; }
  .field--employee .field__label { padding-right: 26px; }

  .gift-mark {
    position: absolute;
    left: 531px;
    top: 250px;
    width: 130px;
    display: flex;
    align-items: center;
    gap: 8px;
    font-size: 20px;
    font-weight: 700;
    color: var(--brand-blue);
  }
  .gift-mark__dot {
    width: 22px;
    height: 22px;
    flex: none;
    border-radius: 50%;
    background: var(--sun-yellow);
  }
</style>
</head>
<body>

<section class="card card--business" aria-label="Business card">
  <h1 class="brand-name">TILLOW MARSH</h1>
  <div class="divider"></div>
  <ul class="contact">
    <li>482 Larkfield Ave.</li>
    <li>Harbor Bend, MI 48731</li>
    <li>
      <svg viewBox="0 0 24 24" aria-hidden="true"><path d="M6.6 10.8a15.1 15.1 0 0 0 6.6 6.6l2.2-2.2a1 1 0 0 1 1-.25 11.4 11.4 0 0 0 3.6.57 1 1 0 0 1 1 1V20a1 1 0 0 1-1 1A17 17 0 0 1 3 4a1 1 0 0 1 1-1h3.5a1 1 0 0 1 1 1c0 1.25.2 2.45.57 3.57a1 1 0 0 1-.25 1z"/></svg>
      989.517.4296
    </li>
    <li>
      <svg viewBox="0 0 24 24" aria-hidden="true"><path d="M2 5h20v14H2z M2 5l10 8 10-8" fill="var(--ink)"/><path d="M3 6l9 7 9-7" fill="none" stroke="#fff" stroke-width="1.6"/></svg>
      Office@TillowMarsh.com
    </li>
  </ul>
  <ul class="offerings">
    <li>Gourmet Food</li>
    <li>Fine Wines | Gift Baskets</li>
    <li>Kitchen &amp; Bath Accessories</li>
    <li>Candles | Cards | Soaps</li>
  </ul>
</section>

<section class="card card--gift" aria-label="Gift card back">
  <div class="card-number">Card Number : 58724</div>
  <div class="field field--large field--to"><span class="field__label">To :</span><span class="field__line"></span></div>
  <div class="field field--large field--from"><span class="field__label">Form :</span><span class="field__line"></span></div>
  <div class="field field--small field--issued"><span class="field__label">Date&nbsp; Issued :</span><span class="field__line"></span></div>
  <div class="field field--small field--expires"><span class="field__label">Expiration Date :</span><span class="field__line"></span></div>
  <div class="field field--small field--employee"><span class="field__label">Employee :</span><span class="field__line"></span></div>
  <div class="gift-mark"><span class="gift-mark__dot"></span><span>Tillow Marsh</span></div>
</section>

</body>
</html>
```